Information One Page for Email

I am looking for a informative attachment I can send with an introductive email for Meridale Slab Works. Something I can also Mail.

Meridale Slab Works is the leader in Rebar Post Tension Cable Placement and Post Tension Cable repair. Outside of cable placement and repair we do concrete repair, Parking Garage restoration and
Updates

Content

Post Tension Repair and Concrete Restoration
Post-tensioning is a revolutionary method in concrete construction that enhances the strength and durability of structures. However, like all construction ele-ments, post-tension cables can experience wear and damage over time. Ensuring timely and effective repair is crucial for maintaining the safety and integrity of your building.
Why Post-Tension Cable Repair is Essential
1. **Structural Integrity**: Damaged or deteriorated cables can compromise the structural integrity of your building, leading to safety hazards and potential structural failures.
2. **Extended Lifespan**: Regular maintenance and repair of post-tension cables extend the lifespan of your structure, ensuring it remains safe and function-al for years to come.
3. **Cost-Effective**: Addressing cable issues early on prevents more severe damage and costly repairs down the line.
Common Signs of Post-Tension Cable Issues
- Cracks in concrete surfaces
- Unusual noises or popping sounds
- Visible cable ends or broken strands
- Water leakage through cracks
Our Repair Process
1. **Inspection and Assessment**: Our team conducts a thorough inspection to identify the extent of the damage and determine the appropriate repair meth-ods.
2. **Cable Repair or Replacement**: Depending on the severity, we either re-pair the existing cables or replace them with new ones to restore full functional-ity.
3. **Sealing and Protection**: After repairing, we seal the affected areas to protect against moisture and future damage.
4. **Quality Assurance**: We perform rigorous quality checks to ensure the repairs meet industry standards and the structure is safe for use.
Why Choose Us
- **Expertise and Experience**: With years of experience in post-tension cable repair, our team is skilled in handling even the most complex repairs efficiently and effectively.
- **Advanced Technology**: We use the latest technology and materials to ensure durable and long-lasting repairs.
- **Customer Satisfaction**: Our commitment to quality and customer satisfaction sets us apart. We work closely with our clients to ensure their needs are met and expectations exceeded.
Contact Us
If you suspect issues with your post-tension cables or need a routine inspection, don't hesitate to contact us. Our experts are ready to provide the best solutions to keep your structures safe and secure.
Ensure the safety and longevity of your building with our professional post-tension cable repair services. Trust us to deliver quality and reliability every time.

```html
<!DOCTYPE html>
<html lang="en">
<head>
<meta charset="utf-8">
<title>Meridale Slab Works – Post Tension Repair &amp; Concrete Restoration</title>
<link href="https://fonts.googleapis.com/css2?family=Arvo:wght@400;700&family=Poppins:wght@400;500&display=swap" rel="stylesheet">
<style>
:root{
  --green:#00753a;
  --green-dark:#064a29;
  --ink:#1f1f1f;
  --charcoal:#262626;
  --slate:#3a3a3c;
  --mist:#e6e6e6;
  --paper:#ffffff;
  --muted:#b9b9b9;
}
*{margin:0;padding:0;box-sizing:border-box}
html,body{width:1200px;height:2785px;overflow:hidden;background:var(--paper)}
body{font-family:"Poppins",sans-serif;color:var(--ink)}
.sheet{position:absolute;left:105px;top:100px;width:992px;height:2584px;background:var(--paper);overflow:hidden}
.abs{position:absolute}
.slab{font-family:"Arvo",serif;font-weight:700}

.hero-photo{left:500px;top:0;width:492px;height:499px;background:linear-gradient(120deg,#ffffff 0%,#e4e4e4 30%,#b8b8b8 60%,#8a8a8a 85%,#6e6e6e 100%)}
.brand{left:73px;top:78px;display:flex;align-items:center;gap:14px}
.brand-square{width:34px;height:34px;background:var(--green)}
.brand-name{font-family:"Arvo",serif;font-weight:700;font-size:34px;color:var(--green);line-height:1}
.hero-title{left:75px;top:226px;font-size:49px;line-height:48px;color:var(--green)}
.intro-band{left:0;top:343px;width:992px;height:156px;background:var(--charcoal)}
.intro-band .hero-photo-edge{position:absolute;left:640px;top:0;width:352px;height:156px;background:linear-gradient(90deg,var(--charcoal),#7a7a7a)}
.intro-text{left:75px;top:376px;width:560px;font-size:16px;line-height:20px;color:#fff}

.section-title{left:0;width:992px;text-align:center;font-size:36px;line-height:40px}
.section-title.green{color:var(--green)}
.band{left:0;width:992px;background:var(--mist)}

.icon-tile{width:93px;height:93px;display:flex;align-items:center;justify-content:center}
.icon-tile.dark{background:var(--charcoal)}
.icon-tile.green{background:var(--green)}
.icon-tile svg{width:62px;height:62px;fill:none;stroke:#fff;stroke-width:2.4;stroke-linecap:round;stroke-linejoin:round}

.feature{width:300px;text-align:center}
.feature h3{font-family:"Arvo",serif;font-weight:700;font-size:30px;line-height:31px}
.feature p{margin-top:16px;font-size:16px;line-height:20px}
.benefit h3{color:var(--green)}
.reason h3{color:var(--ink)}

.sign{width:178px;height:206px;border-top:6px solid var(--green)}
.sign .sign-photo{height:129px}
.sign .sign-label{height:71px;display:flex;align-items:center;justify-content:center;text-align:center;color:#fff;font-size:16px;line-height:20px}
.sign.light .sign-label{background:var(--green)}
.sign.deep .sign-label{background:var(--green-dark)}
.sign.deep{border-top-color:var(--green-dark)}

.step{left:66px;width:864px;height:100px;border-radius:10px;color:#fff;display:flex;align-items:center}
.step.light{background:var(--green)}
.step.deep{background:var(--green-dark)}
.step-name{width:262px;padding-left:35px;font-family:"Arvo",serif;font-weight:700;font-size:24px;line-height:30px}
.step-num{width:69px;height:69px;background:#fff;border-radius:8px;color:var(--ink);font-family:"Arvo",serif;font-weight:700;font-size:46px;display:flex;align-items:center;justify-content:center}
.step-text{margin-left:30px;width:470px;font-size:16px;line-height:20px}

.contact-band{left:0;top:2218px;width:992px;height:127px;background:var(--green);display:flex;align-items:center;justify-content:center;text-align:center;color:#fff;font-size:20.5px;line-height:26px;padding:0 60px}
.closing-band{left:0;top:2345px;width:992px;height:239px;background:var(--slate)}
.closing-text{left:0;top:2373px;width:992px;text-align:center;color:var(--muted);font-size:21px;line-height:26px;text-transform:uppercase}
.call-pill{left:66px;top:2478px;width:858px;height:59px;border-radius:30px;background:var(--green);color:#fff;font-size:30px;display:flex;align-items:center;justify-content:center}
</style>
</head>
<body>
<main class="sheet">
  <div class="abs hero-photo" role="img" aria-label="Grayscale photo of a worker repairing a post-tensioned concrete edge with exposed cable anchorages"></div>
  <div class="abs brand"><span class="brand-square"></span><span class="brand-name">Meridale Slab Works</span></div>
  <h1 class="abs hero-title slab">Post Tension Repair &amp;<br>Concrete Restoration</h1>
  <div class="abs intro-band"><div class="hero-photo-edge" role="img" aria-label="Continuation of the concrete repair photo"></div></div>
  <p class="abs intro-text">Post-tensioning is a revolutionary method in concrete construction that enhances the strength and durability of structures. However, like all construction ele-ments, post-tension cables can experience wear and damage over time. Ensuring timely and effective repair is crucial for maintaining the safety and integrity of your building.</p>

  <h2 class="abs section-title green slab" style="top:542px">Why Post-Tension Cable Repair is Essential</h2>
  <div class="abs band" style="top:657px;height:291px"></div>

  <div class="abs icon-tile dark" style="left:140px;top:612px"><svg viewBox="0 0 64 64"><path d="M8 56h48M14 56V22l24-12v46M38 18l14 6v32M20 28h12M20 36h12M20 44h12M44 32v4M44 42v4"/></svg></div>
  <div class="abs icon-tile dark" style="left:466px;top:612px"><svg viewBox="0 0 64 64"><path d="M18 26c-6-4-10-8-10-12a5 5 0 0 1 10-2 5 5 0 0 1 10 2c0 4-4 8-10 12zM32 30h22v18H32zM32 38h22M43 30v-8M43 22c-4-6 2-8 4-4M43 22c4-6 8 0 4 2M6 40h16l-4-4M22 40l-4 4M6 56h52"/></svg></div>
  <div class="abs icon-tile dark" style="left:768px;top:612px"><svg viewBox="0 0 64 64"><circle cx="32" cy="26" r="10"/><path d="M32 20v12M28 23h6a2 2 0 0 1 0 6h-4M18 30V14M14 18l4-4 4 4M46 30V14M42 18l4-4 4 4M32 16V6M28 10l4-4 4 4M6 46l10-6h12l4 4h-10M6 56l14-4h14l16-12-2-4-14 8"/></svg></div>

  <div class="abs feature benefit" style="left:37px;top:733px"><h3>Structural<br>Integrity</h3><p>Damaged or deteriorated cables can compromise the structural integrity of your building, leading to safety hazards and potential structural failures.</p></div>
  <div class="abs feature benefit" style="left:362px;top:733px"><h3>Extended<br>Lifespan</h3><p>Regular maintenance and repair of post-tension cables extend the lifespan of your structure, ensuring it remains safe and function-al for years to come.</p></div>
  <div class="abs feature benefit" style="left:665px;top:733px"><h3>Cost<br>Effective</h3><p style="padding:0 60px">Addressing cable issues early on prevents more severe damage and costly repairs down the line.</p></div>

  <h2 class="abs section-title slab" style="top:982px">Common Signs of Post-Tension Cable Issues</h2>
  <div class="abs sign light" style="left:75px;top:1045px"><div class="sign-photo" role="img" aria-label="Close-up photo of a crack in a concrete surface" style="background:linear-gradient(160deg,#a8a8a4,#7d7d79)"></div><div class="sign-label">Cracks in<br>concrete surfaces</div></div>
  <div class="abs sign deep" style="left:296px;top:1045px"><div class="sign-photo" role="img" aria-label="Illustration of green sound waves on a black background" style="background:linear-gradient(180deg,#0a0a0a,#1f5a3a 55%,#0a0a0a)"></div><div class="sign-label">Unusual noises<br>or popping sounds</div></div>
  <div class="abs sign light" style="left:523px;top:1045px"><div class="sign-photo" role="img" aria-label="Photo of blue post-tension cables laid across a slab deck" style="background:linear-gradient(160deg,#6b8fb0,#8a7a6a)"></div><div class="sign-label">Visible cable ends<br>or broken strands</div></div>
  <div class="abs sign deep" style="left:745px;top:1045px"><div class="sign-photo" role="img" aria-label="Photo of damaged concrete with water leaking through cracks" style="background:linear-gradient(170deg,#6e5f4f,#3a3530)"></div><div class="sign-label">Water leakage<br>through cracks</div></div>

  <h2 class="abs section-title slab" style="top:1285px">Our Repair Process</h2>
  <div class="abs step light" style="top:1343px"><div class="step-name">Inspection &amp;<br>Assessment</div><div class="step-num">1</div><p class="step-text">Our team conducts a thorough inspection to identify the extent of the damage and determine the appropriate repair meth-ods.</p></div>
  <div class="abs step deep" style="top:1456px"><div class="step-name">Cable Repair or<br>Replacement</div><div class="step-num">2</div><p class="step-text">Depending on the severity, we either re-pair the existing cables or replace them with new ones to restore full functional-ity.</p></div>
  <div class="abs step light" style="top:1570px"><div class="step-name">Sealing and<br>Protection</div><div class="step-num">3</div><p class="step-text">After repairing, we seal the affected areas to protect against moisture and future damage.</p></div>
  <div class="abs step deep" style="top:1683px"><div class="step-name">Quality<br>Assurance</div><div class="step-num">4</div><p class="step-text">We perform rigorous quality checks to ensure the repairs meet industry standards and the structure is safe for use.</p></div>

  <h2 class="abs section-title slab" style="top:1823px">Why Choose Us</h2>
  <div class="abs band" style="top:1937px;height:281px"></div>

  <div class="abs icon-tile green" style="left:142px;top:1890px"><svg viewBox="0 0 64 64"><circle cx="32" cy="38" r="18"/><circle cx="32" cy="34" r="5"/><path d="M23 48c2-6 16-6 18 0M32 6l2 4 4 .5-3 3 1 4-4-2-4 2 1-4-3-3 4-.5zM16 12l1.5 3 3 .4-2.2 2 .6 3-2.9-1.5-2.9 1.5.6-3-2.2-2 3-.4zM48 12l1.5 3 3 .4-2.2 2 .6 3-2.9-1.5-2.9 1.5.6-3-2.2-2 3-.4z"/></svg></div>
  <div class="abs icon-tile green" style="left:438px;top:1890px"><svg viewBox="0 0 64 64"><circle cx="28" cy="38" r="14"/><rect x="22" y="32" width="12" height="12"/><path d="M28 20v4M28 52v4M10 38h4M42 38h4M15 25l3 3M38 48l3 3M15 51l3-3M46 30V8M40 14l6-6 6 6"/></svg></div>
  <div class="abs icon-tile green" style="left:754px;top:1890px"><svg viewBox="0 0 64 64"><path d="M32 6v6M20 10l3 5M44 10l-3 5M32 18l2.5 5 5.5.8-4 3.9 1 5.5-5-2.6-5 2.6 1-5.5-4-3.9 5.5-.8zM16 28l2 4 4 .6-3 2.8.7 4-3.7-2-3.7 2 .7-4-3-2.8 4-.6zM48 28l2 4 4 .6-3 2.8.7 4-3.7-2-3.7 2 .7-4-3-2.8 4-.6zM8 56V46l6-4 4 4v10M26 56V44l6-4 6 4v12M46 56V46l4-4 6 4v10"/></svg></div>

  <div class="abs feature reason" style="left:38px;top:1997px;width:302px"><h3>Expertise<br>&amp; Experience</h3><p>With years of experience in post-tension cable repair, our team is skilled in handling even the most complex repairs efficiently and</p></div>
  <div class="abs feature reason" style="left:334px;top:1997px"><h3>Advanced<br>Technology</h3><p style="padding:0 25px">We use the latest technology and materials to ensure durable and long-lasting repairs.</p></div>
  <div class="abs feature reason" style="left:645px;top:1997px;width:310px"><h3>Customer<br>Satisfaction</h3><p style="margin-top:10px">Our commitment to quality and customer satisfaction sets us apart. We work closely with our clients to ensure their needs are met and expectations exceeded.</p></div>

  <div class="abs contact-band slab">If you suspect issues with your post-tension cables or need a routine inspection, don't hesitate to contact us. Our experts are ready to provide the best solutions to keep your structures safe and secure.</div>
  <div class="abs closing-band"></div>
  <p class="abs closing-text">Ensure the safety and longevity of your building with our<br>professional post-tension cable repair services.<br>Trust us to deliver quality and reliability every time.</p>
  <div class="abs call-pill slab">Call (555) 014-2286 to start your construction project!</div>
</main>
</body>
</html>
```